Business card for Luxury Portable Restroom Trailer company

We are a Luxury Portable Restroom Trailer Company Called FALCRIDGE HIRES. Based in Orange County California. We provide portable restroom trailers for events, such as, Weddings, Concerts, Charity events, Sporting events, Tournaments, Corporate events, ect. We rent and Sell the Luxury restrooms. Our colors are white, grey, and Orange. As you will see in the logo we uploaded.
There are 2 people in the company so the names and titles will change for the 3 people but card will remain the same. Here is the information for each Person: Dwight Penner CFO 555 318-0476
next Person: Leon Marchetti VP 555 318-0476
Next Person: Owen Marchetti CEO 555 318-0476
Information to include on the card: Luxury Restroom Trailers Rental and Sales. Weddings, Concerts, Charity, Sporting and Corp. Events.

```html
<!DOCTYPE html>
<html lang="en">
<head>
<meta charset="utf-8">
<title>Falcridge Hires – Business Card</title>
<link rel="stylesheet" href="https://fonts.googleapis.com/css2?family=Saira+Condensed:wght@300;400;700&display=swap">
<style>
  :root {
    --page: #2b2b2d;
    --card: #f6f6f6;
    --card-edge: #e6e6e6;
    --orange: #e8621c;
    --grey: #4a4a4c;
    --grey-soft: #6a6a6c;
    --mark-tone: #e4e4e4;
  }
  * { box-sizing: border-box; margin: 0; padding: 0; }
  html, body {
    width: 1200px; height: 900px; overflow: hidden;
    background: var(--page);
    font-family: "Saira Condensed", "Arial Narrow", sans-serif;
  }
  .sheet {
    position: relative; width: 1200px; height: 900px;
    display: flex; flex-direction: column; align-items: center; justify-content: center; gap: 24px;
  }
  .card {
    position: relative; width: 700px; height: 400px;
    background: linear-gradient(160deg, #ffffff 0%, var(--card) 55%, var(--card-edge) 100%);
    overflow: hidden;
  }
  .brand-mark {
    position: absolute; right: -40px; top: 30px; width: 330px; height: 250px;
    background: radial-gradient(ellipse at 60% 45%, var(--mark-tone) 0%, rgba(228,228,228,0.6) 55%, rgba(228,228,228,0) 75%);
  }
  .brand {
    position: absolute; display: flex; align-items: center; gap: 12px;
    color: var(--orange); font-weight: 700; letter-spacing: 2px; white-space: nowrap;
  }
  .brand-square { width: 22px; height: 22px; background: var(--orange); flex: none; }
  .card-front .brand { left: 90px; top: 168px; font-size: 54px; }
  .card-front .brand-square { width: 30px; height: 30px; }
  .card-back .brand { left: 50px; top: 50px; font-size: 44px; }

  .contact { position: absolute; left: 60px; top: 205px; width: 600px; }
  .contact-line { display: flex; align-items: center; gap: 8px; color: var(--grey); }
  .person-name { font-weight: 700; font-size: 30px; letter-spacing: 0.5px; text-transform: uppercase; }
  .divider { font-weight: 700; font-size: 28px; }
  .phone { display: flex; align-items: center; gap: 6px; font-weight: 300; font-size: 26px; color: var(--grey-soft); }
  .phone svg { width: 14px; height: 22px; }
  .role-row { display: flex; align-items: center; gap: 10px; margin-top: -4px; }
  .person-role { color: var(--orange); font-weight: 300; font-size: 24px; }
  .role-rule { flex: 1; height: 1px; background: var(--orange); opacity: 0.8; }

  .services { position: absolute; left: 60px; top: 292px; color: var(--grey-soft); }
  .services-title { color: var(--orange); font-weight: 700; font-size: 22px; text-transform: uppercase; letter-spacing: 0.5px; }
  .services-list { font-weight: 300; font-size: 21px; line-height: 1.15; }
  .sep { color: var(--orange); font-weight: 400; padding: 0 4px; }
</style>
</head>
<body>
<main class="sheet">
  <section class="card card-front">
    <div class="brand-mark" role="img" aria-label="Faint brand mark decoration in light grey"></div>
    <div class="brand"><span class="brand-square"></span>FALCRIDGE HIRES</div>
  </section>

  <section class="card card-back">
    <div class="brand-mark" role="img" aria-label="Faint brand mark decoration in light grey"></div>
    <div class="brand"><span class="brand-square"></span>FALCRIDGE HIRES</div>

    <div class="contact">
      <div class="contact-line">
        <span class="person-name">Dwight Penner</span>
        <span class="divider">|</span>
        <span class="phone">
          <svg viewBox="0 0 14 22" aria-hidden="true"><rect x="1" y="1" width="12" height="20" rx="2" fill="none" stroke="#e8621c" stroke-width="1.6"/><line x1="5" y1="17.5" x2="9" y2="17.5" stroke="#e8621c" stroke-width="1.6"/></svg>
          555 318-0476
        </span>
      </div>
      <div class="role-row">
        <span class="person-role">CFO</span>
        <span class="role-rule"></span>
      </div>
    </div>

    <div class="services">
      <h2 class="services-title">Our Services</h2>
      <p class="services-list">Luxury Restroom Trailers Rental and Sales<span class="sep">|</span>Weddings<span class="sep">|</span>Concerts</p>
      <p class="services-list">Charity<span class="sep">|</span>Sporting and Corp<span class="sep">|</span>Events</p>
    </div>
  </section>
</main>
</body>
</html>
```